Marrowby Water Taxi and Transport Business Card

I need business cards for my new water taxi and freight transport business I have started here in Kodiak Alaska. Kodiak is a remote island in the middle of the gulf of Alaska. There are seven native villages around the island and Kodiak is the #2 fishing port in the United States. We also have the largest Coast Guard Base in the U.S. My company will be providing water taxi and freight transport logistics to the villages and many hunting and fishing lodges as well as remote properties around the island.

I would like a business card that isn't status quo, something that stands out, either in feel or appearance. I do like clean minimal designs but it needs to have the necessary contact info on it.

Target Market(s)

remote lodge / property owners, residents of the many villages around Kodiak and any one wanting to enjoy the great outdoors of Kodiak Alaska

Industry/Entity Type

Business

Contact Information for Business Card

I like clean simple designs that aren't cluttered but still provide the necessary information

Colors
0255a3
3277b5
33a4d5
9bcb3c
add136
fbed22
ffc214
f78f20
f37122

Requirements
Must have
• logo and contact info
• Captain Mason Elwick
• www.marrowbyferryline.com
• mason@marrowbyferryline.com

```html
<!DOCTYPE html>
<html lang="en">
<head>
<meta charset="utf-8">
<title>Marrowby Water Taxi and Transport – Business Card</title>
<link href="https://fonts.googleapis.com/css2?family=Open+Sans:wght@400;600;700&display=swap" rel="stylesheet">
<style>
  :root {
    --navy: #0255a3;
    --blue: #3277b5;
    --sky: #33a4d5;
    --deep: #0a3784;
    --orange: #f78f20;
    --amber: #ffc214;
    --rule: #8a8250;
    --paper: #ffffff;
    --backdrop: #e9ebee;
  }
  * { box-sizing: border-box; margin: 0; padding: 0; }
  html, body { width: 1200px; height: 913px; overflow: hidden; }
  body {
    background: var(--backdrop);
    font-family: "Open Sans", Arial, sans-serif;
    display: flex;
    align-items: center;
    justify-content: center;
    gap: 50px;
  }
  .card {
    position: relative;
    width: 525px;
    height: 300px;
    border-radius: 16px;
    overflow: hidden;
    box-shadow: 0 10px 26px rgba(0,0,0,.18);
  }
  .card-front { background: var(--paper); }
  .card-back { background: linear-gradient(160deg, var(--blue) 0%, var(--navy) 45%, var(--deep) 100%); }

  .card-waves { position: absolute; inset: 0; width: 100%; height: 100%; }

  .brand {
    position: absolute;
    top: 34px;
    left: 0; right: 0;
    display: flex;
    align-items: center;
    justify-content: center;
    gap: 12px;
  }
  .brand-dot {
    width: 26px; height: 26px;
    border-radius: 50%;
    background: var(--orange);
    flex: none;
  }
  .brand-name {
    font-size: 21px;
    font-weight: 600;
    color: var(--navy);
    line-height: 1.2;
    max-width: 250px;
  }

  .contact-icons {
    position: absolute;
    top: 130px; left: 0; right: 0;
    display: flex; justify-content: center; gap: 6px;
  }
  .contact-icons svg { width: 11px; height: 11px; }

  .holder {
    position: absolute;
    top: 144px; left: 0; right: 0;
    text-align: center;
    font-size: 17px;
    font-weight: 700;
    color: var(--navy);
  }
  .divider {
    position: absolute;
    top: 172px; left: 0; right: 0;
    height: 1px;
    background: var(--rule);
  }
  .contact-line {
    position: absolute;
    top: 182px; left: 0; right: 0;
    text-align: center;
    font-size: 11.5px;
    font-weight: 400;
    color: var(--blue);
  }

  .back-artwork {
    position: absolute;
    left: 150px; top: 45px;
    width: 225px; height: 165px;
    border-radius: 12px;
    background: linear-gradient(150deg, var(--amber) 0%, var(--sky) 35%, #c9ced6 70%, var(--sky) 100%);
    opacity: .85;
  }
</style>
</head>
<body>

  <section class="card card-front" aria-label="Business card front">
    <svg class="card-waves" viewBox="0 0 525 300" preserveAspectRatio="none" aria-hidden="true">
      <path d="M0 300 L0 296 C150 292 280 275 380 245 C440 228 490 212 525 205 L525 300 Z" fill="var(--navy)"/>
      <path d="M0 298 C150 294 285 280 385 252 C445 236 490 222 525 216 L525 226 C490 232 445 246 390 262 C290 290 150 298 0 300 Z" fill="var(--sky)"/>
      <path d="M200 285 C290 275 360 258 420 238 C460 225 495 214 520 210 C480 222 450 234 415 248 C355 270 290 282 200 285 Z" fill="var(--paper)" opacity=".55"/>
    </svg>

    <div class="brand">
      <span class="brand-dot"></span>
      <span class="brand-name">Marrowby Water Taxi and Transport</span>
    </div>

    <div class="contact-icons" aria-hidden="true">
      <svg viewBox="0 0 12 12"><rect x="1" y="2.5" width="10" height="7" rx="1" fill="none" stroke="var(--orange)" stroke-width="1.3"/><path d="M1.5 3 L6 6.5 L10.5 3" fill="none" stroke="var(--orange)" stroke-width="1.2"/></svg>
      <svg viewBox="0 0 12 12"><circle cx="6" cy="6" r="5" fill="none" stroke="var(--orange)" stroke-width="1.2"/><ellipse cx="6" cy="6" rx="2.2" ry="5" fill="none" stroke="var(--orange)" stroke-width="1"/><path d="M1 6 H11" stroke="var(--orange)" stroke-width="1"/></svg>
    </div>

    <p class="holder">Captain Mason Elwick</p>
    <div class="divider"></div>
    <p class="contact-line">mason@marrowbyferryline.com - www.marrowbyferryline.com</p>
  </section>

  <section class="card card-back" aria-label="Business card back">
    <svg class="card-waves" viewBox="0 0 525 300" preserveAspectRatio="none" aria-hidden="true">
      <path d="M0 300 L0 290 C150 284 280 266 380 235 C440 216 490 198 525 190 L525 300 Z" fill="var(--orange)"/>
      <path d="M0 292 C150 286 285 270 385 242 C445 224 490 208 525 202 L525 214 C490 220 445 234 390 256 C290 288 150 298 0 300 Z" fill="var(--sky)"/>
      <path d="M180 270 C270 258 340 238 400 214 C445 196 485 182 520 176 C478 192 440 208 400 226 C340 252 270 268 180 270 Z" fill="var(--sky)" opacity=".7"/>
    </svg>
    <div class="back-artwork" role="img" aria-label="Illustration of a grey ferry on waves before icy blue mountains and an orange sun"></div>
  </section>

</body>
</html>
```